Meadowfield Baptist Church Banner Design

Designing 6 banners (3 + 3 that will hang on opposite sides of our auditorium) that are 10 feet long by 4 feet wide.

Use our branding guide - specifically item 4 (vertical logo) and item 5 (icon logo).

Design elements found in our KINDLE booklet, we would like to see designs that utilize the white, green and blue colour palettes but NOT the grey. Other colours may be incorporated (e.g. coral).

We are looking for 3 banner designs that would match on either side of the auditorium, the first banner incorporating the word "TRUTH", the second incorporating the word "LOVE", and the third incorporating the word "MISSION".

We interested in incorporating graphics such as trees or outdoor themes.

Font styles to use
Other font styles liked:
• Montserrat

Colors
34a7d7
00a990
f47c35

Requirements
Must have
• Banner Type #1 include the word "TRUTH"
Banner Type #2 include the word "LOVE"
Banner Type #3 include the word "MISSION"

Colour scheme must include CMYK 54 / 5 / 16 / 0 (which is available in the branding guide.) We have selected the three colours, included below in the brief.

From the branding guide - utilize #5 (icon) for the banner.

UPDATE: After reviewing the initial submissions, we are asking for designs that ONLY incorporate #5 - the ICON logo for the banners.
Nice to have
• It would be nice to have some creativity with the colour ... though a more minimalistic style is preferred.

Graphic adaptations such as trees in the background would be of interest.
Should not have
• Colour scheme should not be gray scale.

The banners should NOT be too busy.

Scripture verses (written out) are not necessary.

```html
<!DOCTYPE html>
<html lang="en">
<head>
<meta charset="utf-8">
<title>Meadowfield Baptist Church — Auditorium Banners</title>
<link href="https://fonts.googleapis.com/css2?family=Montserrat:wght@800;900&display=swap" rel="stylesheet">
<style>
  :root {
    --sky-blue: #34a7d7;
    --green: #00a990;
    --coral: #f47c35;
    --white: #ffffff;
    --paint-deep: #1a78a8;
    --paint-mid: #2a93c4;
    --paint-light: #6fd2ea;
  }
  html, body {
    margin: 0;
    padding: 0;
    width: 1200px;
    height: 923px;
    overflow: hidden;
    background: var(--white);
    font-family: "Montserrat", Arial, sans-serif;
  }
  .banner-set {
    position: relative;
    width: 1200px;
    height: 923px;
  }
  .banner {
    position: absolute;
    top: 19px;
    width: 353px;
    height: 882px;
    overflow: hidden;
  }
  .banner--truth { left: 24px; }
  .banner--love { left: 434px; }
  .banner--mission { left: 823px; }

  .banner__paint {
    position: absolute;
    inset: 0;
    background:
      linear-gradient(178deg, transparent 0%, transparent 58%, rgba(111,210,234,0.55) 68%, transparent 76%),
      linear-gradient(182deg, transparent 30%, rgba(111,210,234,0.35) 40%, transparent 48%),
      linear-gradient(180deg, var(--paint-mid) 0%, var(--paint-deep) 45%, var(--paint-mid) 100%);
  }
  .banner--love .banner__paint {
    background:
      linear-gradient(180deg, transparent 28%, rgba(111,210,234,0.8) 34%, rgba(111,210,234,0.35) 45%, transparent 55%),
      linear-gradient(180deg, var(--paint-mid) 0%, var(--paint-deep) 55%, var(--paint-mid) 100%);
  }

  .banner__block {
    position: absolute;
    left: 0;
    right: 0;
    height: 247px;
    display: flex;
    align-items: center;
    justify-content: center;
  }
  .banner__block--bottom { bottom: 0; }
  .banner__block--top { top: 0; }
  .banner__block--blue { background: var(--sky-blue); }
  .banner__block--green { background: var(--green); }
  .banner__block--coral { background: var(--coral); }

  .church-name {
    margin: 0;
    color: var(--white);
    font-weight: 800;
    font-size: 25px;
    line-height: 1.15;
    text-align: center;
    text-transform: uppercase;
    letter-spacing: 0.02em;
  }

  .banner__frame {
    position: absolute;
    inset: 19px;
    border: 6px solid var(--white);
    pointer-events: none;
  }

  .banner__word {
    position: absolute;
    left: 50%;
    margin: 0;
    color: var(--white);
    font-weight: 900;
    font-size: 127px;
    line-height: 1;
    white-space: nowrap;
    transform: translate(-50%, -50%) rotate(-90deg);
  }
  .banner--truth .banner__word { top: 340px; }
  .banner--love .banner__word { top: 573px; }
  .banner--mission .banner__word { top: 345px; }
</style>
</head>
<body>
  <main class="banner-set">
    <section class="banner banner--truth">
      <div class="banner__paint" role="img" aria-label="Blue painted brushstroke texture"></div>
      <div class="banner__block banner__block--bottom banner__block--blue">
        <p class="church-name">Meadowfield<br>Baptist<br>Church</p>
      </div>
      <div class="banner__frame"></div>
      <h2 class="banner__word">TRUTH</h2>
    </section>

    <section class="banner banner--love">
      <div class="banner__paint" role="img" aria-label="Blue painted brushstroke texture"></div>
      <div class="banner__block banner__block--top banner__block--green">
        <p class="church-name">Meadowfield<br>Baptist<br>Church</p>
      </div>
      <div class="banner__frame"></div>
      <h2 class="banner__word">LOVE</h2>
    </section>

    <section class="banner banner--mission">
      <div class="banner__paint" role="img" aria-label="Blue painted brushstroke texture"></div>
      <div class="banner__block banner__block--bottom banner__block--coral">
        <p class="church-name">Meadowfield<br>Baptist<br>Church</p>
      </div>
      <div class="banner__frame"></div>
      <h2 class="banner__word">MISSION</h2>
    </section>
  </main>
</body>
</html>
```